TK Homes - Stone Dorf Design

Looking for a double sides design, 1 side for my realestate and the other for home building. ( TK Homes on 1 side, Stone Dorf card on the other Side
Side 1 - Marek Tove ~ Vox Realty logo and Company ( the Property quarter )
Marek Tove
Marek@Marektove.example
IG - Marek_Bzq_Realtor
FB - marekt
Cell - 5558130467
3847 61 St Nw

Side 2
Marek Tove
5558130467
IG - Stonedorf_Bzq
Stonedorfdev@mailbox.example

Target Market(s)

Home buyers/ sellers

Industry/Entity Type

Home builders - Realestate

Contact Information for Business Card

Above

Requirements
Must have
• Black OR White background - my information -

```html
<!DOCTYPE html>
<html lang="en">
<head>
<meta charset="utf-8">
<title>Marek Tove – Business Cards</title>
<link rel="stylesheet" href="https://fonts.googleapis.com/css2?family=Tinos:wght@400;700&display=swap">
<style>
  :root {
    --page-bg: #232323;
    --card-bg: #202024;
    --brand-blue: #0b72c0;
    --brand-yellow: #f5c534;
    --text-white: #ffffff;
  }
  * { margin: 0; padding: 0; box-sizing: border-box; }
  html, body {
    width: 1200px; height: 780px; overflow: hidden;
    background: var(--page-bg);
    font-family: "Tinos", "Times New Roman", serif;
  }
  .canvas { position: relative; width: 1200px; height: 780px; }

  .card {
    position: absolute;
    width: 620px; height: 354px;
    background: var(--card-bg);
    border-bottom: 5px solid var(--brand-yellow);
    box-shadow: 0 10px 24px rgba(0,0,0,0.55);
  }
  .card--builder { left: 120px; top: 24px; }
  .card--realty { left: 460px; top: 402px; }

  .card__divider {
    position: absolute; left: 318px; top: 70px;
    width: 2px; height: 200px; background: var(--text-white);
  }

  .brand-mark {
    position: absolute; left: 24px; width: 270px; top: 0; height: 100%;
    display: flex; align-items: center; justify-content: center; gap: 10px;
  }
  .brand-mark__square {
    width: 12px; height: 12px; background: var(--brand-yellow); flex: none;
  }
  .brand-mark__name {
    font-weight: 400; font-size: 30px; color: var(--text-white);
    white-space: nowrap;
  }

  .contact {
    position: absolute; left: 360px; top: 70px; width: 250px;
    color: var(--text-white);
  }
  .contact__name { font-weight: 700; font-size: 30px; line-height: 1; }
  .contact__first { color: var(--brand-blue); }
  .contact__last { color: var(--brand-yellow); }
  .contact__role { font-weight: 700; font-size: 14px; margin-top: 4px; }
  .contact__list { list-style: none; margin-top: 16px; }
  .contact__item {
    display: flex; align-items: center; gap: 8px;
    font-size: 13px; line-height: 1.6; white-space: nowrap;
  }
  .contact__icon { width: 13px; height: 13px; flex: none; }
  .contact__dot {
    width: 11px; height: 11px; margin: 0 1px; flex: none;
    border: 2px solid var(--brand-blue); border-radius: 50%;
  }

  .card__address {
    position: absolute; left: 360px; bottom: 28px;
    color: var(--text-white); font-size: 15px;
  }
</style>
</head>
<body>
<main class="canvas">

  <section class="card card--builder" aria-label="Stone Dorf builder card">
    <div class="brand-mark">
      <span class="brand-mark__square"></span>
      <span class="brand-mark__name">Stone Dorf</span>
    </div>
    <div class="card__divider"></div>
    <div class="contact">
      <p class="contact__name"><span class="contact__first">Marek</span> <span class="contact__last">Tove</span></p>
      <p class="contact__role">Director</p>
      <ul class="contact__list">
        <li class="contact__item">
          <svg class="contact__icon" viewBox="0 0 24 24"><path fill="#0b72c0" d="M6.6 10.8a15 15 0 0 0 6.6 6.6l2.2-2.2a1 1 0 0 1 1-.25 11.4 11.4 0 0 0 3.6.57 1 1 0 0 1 1 1V20a1 1 0 0 1-1 1A17 17 0 0 1 3 4a1 1 0 0 1 1-1h3.5a1 1 0 0 1 1 1c0 1.25.2 2.45.57 3.6a1 1 0 0 1-.25 1z"/></svg>
          5558130467
        </li>
        <li class="contact__item"><span class="contact__dot"></span>Stonedorf_Bzq</li>
        <li class="contact__item">
          <svg class="contact__icon" viewBox="0 0 24 24"><path fill="#0b72c0" d="M2 5h20v14H2z"/><path fill="none" stroke="#202024" stroke-width="1.6" d="M2 5l10 8 10-8"/></svg>
          Stonedorfdev@mailbox.example
        </li>
      </ul>
    </div>
  </section>

  <section class="card card--realty" aria-label="Marek Tove realty card">
    <div class="brand-mark">
      <span class="brand-mark__name">Marek Tove</span>
    </div>
    <div class="card__divider"></div>
    <div class="contact">
      <p class="contact__name"><span class="contact__first">Marek</span> <span class="contact__last">Tove</span></p>
      <p class="contact__role">Director</p>
      <ul class="contact__list">
        <li class="contact__item">
          <svg class="contact__icon" viewBox="0 0 24 24"><path fill="#0b72c0" d="M6.6 10.8a15 15 0 0 0 6.6 6.6l2.2-2.2a1 1 0 0 1 1-.25 11.4 11.4 0 0 0 3.6.57 1 1 0 0 1 1 1V20a1 1 0 0 1-1 1A17 17 0 0 1 3 4a1 1 0 0 1 1-1h3.5a1 1 0 0 1 1 1c0 1.25.2 2.45.57 3.6a1 1 0 0 1-.25 1z"/></svg>
          5558130467
        </li>
        <li class="contact__item"><span class="contact__dot"></span>marekt</li>
        <li class="contact__item"><span class="contact__dot"></span>Marek_Bzq_Realtor</li>
        <li class="contact__item">
          <svg class="contact__icon" viewBox="0 0 24 24"><path fill="#0b72c0" d="M2 5h20v14H2z"/><path fill="none" stroke="#202024" stroke-width="1.6" d="M2 5l10 8 10-8"/></svg>
          Marek@Marektove.example
        </li>
        <li class="contact__item">
          <svg class="contact__icon" viewBox="0 0 24 24"><g fill="none" stroke="#0b72c0" stroke-width="2"><circle cx="12" cy="12" r="10"/><ellipse cx="12" cy="12" rx="4.5" ry="10"/><path d="M2 12h20M4 6.5h16M4 17.5h16"/></g></svg>
          www.marektove.example
        </li>
      </ul>
    </div>
    <p class="card__address">3847 61 St Nw</p>
  </section>

</main>
</body>
</html>
```